Design for the A4 Letterhead, envelope and A4 Folder

Design have to be clean, professional, unique (eye catchy) and high end.
Colors: Yellow (Code: 803C), Darker Grey and Black or white (optional)
Logo can be in white or black

Letterhead:
Contain: 1. Korvane Logo
2. Slogan "MADE WITH PRIDE"
3. Company information:
Korvane Valves Pte. Ltd. (Singapore)
Registration no: 201947215K
Tel: (65) 6418 2904
Fax: (65) 6472 9186
Email: sales@korvanevalves.example
Website: http://www.korvanevalves.example
4. Logo watermark

Envelope:
Contain: 1. Korvane Logo
3. website: http://www.korvanevalves.example and email address:
sales@korvanevalves.example
4. Logo watermark

Folder:
Contain: 1. Korvane Logo
3. Company's information:
Tel: (65) 6418 2904
Fax: (65) 6472 9186
4. QR Code
5. Logo watermark
6. On the inside there is a space to insert business card. Contrast colors
between the inside and cover.
Updates

For the Folder design, please be informed that we would prefer to have the Korvane logo on the left hand side of the cover page, rather than on the right hand side.And also if we could highlight the "Made with Pride" slogan with either the yellow box or black/grey box depending on the background color.For the Envelope design,it does not matter where the position of the logo is. But please also highlight the "Made with Pride" Slogan For the Letterhead design, the position of the logo must be on the left hand side and the slogan must be highlighted. In addition, please include the following company information (only for the letterhead design)Korvane Valves Pte. Ltd. (Singapore)Registration no: 200308878MTel: (65) 6535 3735Fax: (65) 6533 3570Email: sales@dynatechpumps.comWebsite: http://www.korvanevalves.example Added Wednesday, August 2, 2017

Target Market(s)

Business to Business, High End market

Industry/Entity Type

It Professional

Font styles to use
Serif

Requirements
Must have
• Design have to be clean, professional, unique (eye catchy) and high end.
Nice to have
• color contrast but still maintaining the professionalism and the seriousness
Should not have
• Messy look, futuristic look, too crowded

```html
<!DOCTYPE html>
<html lang="en">
<head>
<meta charset="utf-8">
<title>Korvane Valves – Letterhead</title>
<link rel="stylesheet" href="https://fonts.googleapis.com/css2?family=PT+Serif:wght@400;700&family=Open+Sans:wght@400;700&display=swap">
<style>
  :root {
    --backdrop: #e4d87c;
    --paper: #ffffff;
    --yellow: #f7e81c;
    --yellow-deep: #f2dc00;
    --black: #111111;
    --grey-dark: #3a3a3a;
    --grey-text: #555555;
    --watermark: #f1f1f1;
  }
  * { box-sizing: border-box; margin: 0; padding: 0; }
  html, body { width: 1200px; height: 784px; overflow: hidden; background: var(--backdrop); }
  .letterhead {
    position: absolute; left: 338px; top: 22px;
    width: 523px; height: 740px;
    background: var(--paper);
    box-shadow: 0 6px 18px rgba(0,0,0,.18);
    overflow: hidden;
  }
  .brand-tab {
    position: absolute; left: 0; top: 0;
    width: 84px; height: 66px;
    background: var(--black);
    border-bottom-right-radius: 14px;
    display: flex; align-items: center; justify-content: center; gap: 5px;
  }
  .brand-tab .mark { width: 10px; height: 10px; border-radius: 50%; background: var(--paper); }
  .brand-tab .name { font-family: "PT Serif", serif; font-weight: 700; font-size: 14px; color: var(--paper); letter-spacing: .5px; }
  .header-rule {
    position: absolute; left: 84px; top: 62px; width: 400px; height: 4px;
    background: linear-gradient(90deg, var(--yellow-deep), var(--yellow) 80%, rgba(247,232,28,.4));
  }
  .header-info { position: absolute; right: 40px; top: 10px; text-align: right; }
  .slogan { font-family: "PT Serif", serif; font-size: 25px; color: var(--yellow-deep); letter-spacing: 1px; line-height: 1; }
  .company { font-family: "Open Sans", sans-serif; font-weight: 700; font-size: 8.5px; color: var(--black); margin-top: 4px; }
  .contacts { font-family: "Open Sans", sans-serif; font-size: 6.5px; color: var(--grey-text); margin-top: 3px; display: flex; gap: 6px; justify-content: flex-end; }
  .contacts span::before {
    content: ""; display: inline-block; width: 5px; height: 5px; border-radius: 50%;
    background: var(--grey-dark); margin-right: 2px; vertical-align: -0.5px;
  }
  .watermark {
    position: absolute; left: 50%; top: 430px; transform: translate(-50%, -50%);
    display: flex; align-items: center; gap: 16px;
  }
  .watermark .mark { width: 70px; height: 70px; border-radius: 50%; background: var(--watermark); }
  .watermark .name { font-family: "PT Serif", serif; font-size: 64px; color: var(--watermark); }
  .footer-band { position: absolute; left: 0; bottom: 0; width: 100%; height: 30px; }
  .footer-band svg { display: block; }
  .reg-no {
    position: absolute; right: 14px; bottom: 8px;
    font-family: "Open Sans", sans-serif; font-weight: 700; font-size: 9px; color: var(--black);
  }
</style>
</head>
<body>
  <main class="letterhead">
    <div class="brand-tab"><span class="mark"></span><span class="name">Korvane</span></div>
    <div class="header-rule"></div>
    <header class="header-info">
      <p class="slogan">MADE WITH PRIDE</p>
      <p class="company">Korvane Valves Pte. Ltd. (Singapore)</p>
      <p class="contacts">
        <span>(65) 6418 2904</span>
        <span>(65) 6472 9186</span>
        <span>sales@korvanevalves.example</span>
        <span>www.korvanevalves.example</span>
      </p>
    </header>
    <div class="watermark" aria-hidden="true"><span class="mark"></span><span class="name">Korvane</span></div>
    <footer class="footer-band">
      <svg width="523" height="30" viewBox="0 0 523 30">
        <path d="M0 22 H372 Q378 22 382 14 Q386 8 394 8 H523 V30 H0 Z" fill="var(--yellow)"/>
        <rect x="0" y="18" width="110" height="3" fill="var(--grey-dark)"/>
        <rect x="110" y="18" width="140" height="3" fill="var(--yellow-deep)"/>
        <rect x="250" y="18" width="118" height="3" fill="var(--grey-dark)"/>
      </svg>
      <p class="reg-no">Regd. No: 201947215K</p>
    </footer>
  </main>
</body>
</html>
```